Purpose, Mission, and Values Poster Update

Crestline Field Laboratories, a Testing, Inspection, and Certification company in the Atlanta area, needs an updated PMV poster. Looking to update graphics and presentation, moving away from current design. Want to carry over company logo, colors (you can include additional blues in the design beyond what is mentioned in the brand guidelines as the previous design did), and messaging (see attachments).

We would also like a companion poster, using the same design language, that shows our goals for leads and won opportunities. Want to carry over logo, colors, and messaging from original, except for this one we want the leads goal to be 115 instead of 85.

Both posters need to be 6000w x 7200h at 300ppi, CMYK. We want to move away from the cartoony, corporate clipart sort of look that the current design has, as new leadership doesn't like the aesthetic.

Target Market(s)

Internal - group of engineers, chemists, scientists, and other technical personnel

Industry/Entity Type

TIC (Testing, Inspection, Certification)

Font styles to use
Serif
Sans Serif

Colors
0054AA
0677BA
7BADD7
CADEEF
E8F1F8

Requirements
Must have
• For both: CMYK colors for printing, 6000w x 7200h at 300ppi for poster sizing leads, company logo; for PMV poster: phrasing of purpose, mission, and values statements preserved; for ring the bell poster: leads goal updated to 115, opportunities goal unchanged at 25
Should not have
• Corporate clipart, cartoon characters

```html
<!DOCTYPE html>
<html lang="en">
<head>
<meta charset="utf-8">
<title>We Ring the Bell — Crestline Field Laboratories</title>
<link rel="stylesheet" href="https://fonts.googleapis.com/css2?family=Anton&family=Archivo:ital,wght@0,500;0,600;1,800;1,900&family=Oswald:wght@200&display=swap">
<style>
  :root {
    --stage: #ecebe8;
    --navy: #1b1f4f;
    --cyan: #46c5e8;
    --mid-blue: #1e6fb0;
    --the-blue: #2183cc;
    --white: #f4f3f1;
    --mist: #a7c4d0;
    --rule: #e9e6e0;
  }
  * { margin: 0; padding: 0; box-sizing: border-box; }
  html, body { width: 1200px; height: 1189px; overflow: hidden; background: var(--stage); }
  .stage { width: 1200px; height: 1189px; display: flex; justify-content: center; align-items: center; }
  .poster { width: 991px; height: 1189px; display: block; background: var(--navy); }
  .kicker { font-family: "Archivo", sans-serif; font-weight: 500; fill: var(--white); }
  .tagline { font-family: "Archivo", sans-serif; font-weight: 800; font-style: italic; fill: var(--cyan); }
  .brand { font-family: "Archivo", sans-serif; font-weight: 600; fill: var(--white); }
  .display { font-family: "Anton", sans-serif; }
  .thin { font-family: "Oswald", sans-serif; font-weight: 200; }
  .lead-in { font-family: "Archivo", sans-serif; font-weight: 900; font-style: italic; }
  .unit { font-family: "Anton", sans-serif; }
</style>
</head>
<body>
<main class="stage">
  <svg class="poster" viewBox="0 0 991 1189" xmlns="http://www.w3.org/2000/svg" role="img" aria-label="We ring the bell: once when we've hit 115 leads, twice when we've won 25 opportunities">
    <rect width="991" height="1189" fill="var(--navy)"/>

    <!-- header -->
    <text class="kicker" x="48" y="105" font-size="27" textLength="440" lengthAdjust="spacingAndGlyphs">Celebrating Our Opportunities to</text>
    <text class="tagline" x="48" y="150" font-size="37" textLength="590" lengthAdjust="spacingAndGlyphs">Create a Safe and Reliable World</text>

    <!-- brand -->
    <rect x="786" y="92" width="22" height="22" fill="var(--white)"/>
    <text class="brand" x="818" y="112" font-size="24">Crestline</text>
    <text class="brand" x="786" y="146" font-size="16" textLength="170" lengthAdjust="spacingAndGlyphs">Field Laboratories</text>

    <!-- headline -->
    <text class="display" transform="translate(232 452) rotate(-90)" font-size="262" fill="var(--cyan)" textLength="255" lengthAdjust="spacingAndGlyphs">WE</text>
    <text class="display" x="244" y="480" font-size="330" fill="var(--white)" textLength="560" lengthAdjust="spacingAndGlyphs">RING</text>
    <text class="thin" x="262" y="662" font-size="215" fill="var(--the-blue)" textLength="176" lengthAdjust="spacingAndGlyphs">THE</text>
    <text class="display" x="452" y="772" font-size="320" fill="var(--cyan)" textLength="500" lengthAdjust="spacingAndGlyphs">BELL</text>

    <!-- dot grids -->
    <g fill="var(--cyan)">
      <g transform="translate(852 300)">
        <circle cx="0" cy="0" r="2.5"/><circle cx="20" cy="0" r="2.5"/><circle cx="40" cy="0" r="2.5"/><circle cx="60" cy="0" r="2.5"/>
        <circle cx="0" cy="20" r="2.5"/><circle cx="20" cy="20" r="2.5"/><circle cx="40" cy="20" r="2.5"/><circle cx="60" cy="20" r="2.5"/>
        <circle cx="0" cy="40" r="2.5"/><circle cx="20" cy="40" r="2.5"/><circle cx="40" cy="40" r="2.5"/><circle cx="60" cy="40" r="2.5"/>
        <circle cx="0" cy="60" r="2.5"/><circle cx="20" cy="60" r="2.5"/><circle cx="40" cy="60" r="2.5"/><circle cx="60" cy="60" r="2.5"/>
      </g>
      <g transform="translate(74 640)">
        <circle cx="0" cy="0" r="2.5"/><circle cx="20" cy="0" r="2.5"/><circle cx="40" cy="0" r="2.5"/><circle cx="60" cy="0" r="2.5"/>
        <circle cx="0" cy="20" r="2.5"/><circle cx="20" cy="20" r="2.5"/><circle cx="40" cy="20" r="2.5"/><circle cx="60" cy="20" r="2.5"/>
        <circle cx="0" cy="40" r="2.5"/><circle cx="20" cy="40" r="2.5"/><circle cx="40" cy="40" r="2.5"/><circle cx="60" cy="40" r="2.5"/>
        <circle cx="0" cy="60" r="2.5"/><circle cx="20" cy="60" r="2.5"/><circle cx="40" cy="60" r="2.5"/><circle cx="60" cy="60" r="2.5"/>
      </g>
    </g>

    <!-- leads goal -->
    <g class="goal goal--leads">
      <rect x="22" y="795" width="438" height="372" fill="var(--cyan)"/>
      <rect x="22" y="1160" width="438" height="7" fill="var(--rule)"/>
      <text class="lead-in" x="241" y="858" font-size="32" fill="var(--navy)" text-anchor="middle">Once when</text>
      <text class="lead-in" x="241" y="892" font-size="32" fill="var(--navy)" text-anchor="middle">we’ve hit</text>
      <text class="display" x="241" y="1084" font-size="186" fill="var(--navy)" text-anchor="middle" textLength="200" lengthAdjust="spacingAndGlyphs">115</text>
      <text class="unit" x="241" y="1124" font-size="32" fill="var(--navy)" text-anchor="middle">LEADS</text>
    </g>

    <!-- opportunities goal -->
    <g class="goal goal--wins">
      <rect x="478" y="795" width="478" height="372" fill="var(--mid-blue)"/>
      <rect x="478" y="1160" width="478" height="7" fill="var(--rule)"/>
      <text class="lead-in" x="717" y="864" font-size="32" fill="var(--mist)" text-anchor="middle">Twice when</text>
      <text class="lead-in" x="717" y="898" font-size="32" fill="var(--mist)" text-anchor="middle">we’ve won</text>
      <text class="display" x="717" y="1090" font-size="186" fill="var(--mist)" text-anchor="middle" textLength="177" lengthAdjust="spacingAndGlyphs">25</text>
      <text class="unit" x="717" y="1138" font-size="32" fill="var(--mist)" text-anchor="middle">OPPORTUNITIES</text>
    </g>
  </svg>
</main>
</body>
</html>
```